Games company needs intuitive redesign for lottery engagement game.

We require the interface of our lottery prediction game to be redesigned not just cosmetically but functionally also. In this game, users are presented with a series of questions relating to the upcoming lottery draw and have to make a binary choice if they think the statement on the card is true or false (Y/N). This prediction dynamic forms the crux of our game and should be maintained but colours, branding and method of interaction are all free to be changed Designers should note that the red text boxes on the briefing screens would not be present in the final product and are only there to clarify app functionality. App screens progress chronologically from 1-12 Any further questions or queries that would aid design works please message directly.

```html
<!DOCTYPE html>
<html lang="en">
<head>
<meta charset="utf-8">
<title>Draw Quiz – Intro</title>
<link href="https://fonts.googleapis.com/css2?family=Poppins:wght@300;400;500;600&display=swap" rel="stylesheet">
<style>
  :root{
    --pink:#f76d8f;
    --rose-bg:#c27080;
    --grey-bg:#c5c5c5;
    --green:#9bb174;
    --navy:#2f2f4b;
    --plum:#544450;
    --ink:#555058;
    --white:#ffffff;
  }
  *{margin:0;padding:0;box-sizing:border-box}
  html,body{width:1200px;height:2403px;overflow:hidden}
  body{font-family:'Poppins',sans-serif;background:var(--grey-bg);position:relative}
  .backdrop{position:absolute;inset:0;overflow:hidden}
  .backdrop .band-top{position:absolute;left:0;top:0;width:1200px;height:1110px;background:var(--rose-bg)}
  .backdrop .band-fade{position:absolute;left:0;top:1040px;width:1200px;height:140px;background:linear-gradient(var(--rose-bg),var(--grey-bg))}
  .backdrop .band-bottom{position:absolute;left:0;top:2060px;width:1200px;height:343px;background:linear-gradient(#5a5a66,var(--navy) 25%)}
  .blur{position:absolute;filter:blur(22px);border-radius:40px}
  .backdrop .bar-a{left:270px;top:120px;width:290px;height:60px;background:#cc909d}
  .backdrop .bar-b{left:150px;top:330px;width:900px;height:50px;background:#c98595}
  .backdrop .bar-c{left:260px;top:440px;width:500px;height:60px;background:#b0667a}
  .backdrop .side-l{left:40px;top:1080px;width:90px;height:420px;background:var(--green)}
  .backdrop .side-r{left:1080px;top:1080px;width:90px;height:420px;background:var(--green)}
  .backdrop .pill{left:380px;top:1900px;width:440px;height:130px;border-radius:70px;background:var(--green)}
  .backdrop .glow{left:330px;top:2190px;width:560px;height:160px;background:#8a5a92}

  .modal{position:absolute;left:85px;top:572px;width:1031px;height:1170px;background:var(--white);border-radius:58px;overflow:hidden;box-shadow:0 10px 40px rgba(0,0,0,.12)}
  .modal-title{position:absolute;left:0;width:870px;top:645px;text-align:center;color:var(--pink);font-weight:600;font-size:67px;line-height:88px}
  .close-btn{position:absolute;left:950px;top:632px;width:120px;height:120px}
  .brand-badge{position:absolute;left:155px;top:823px;width:222px;height:222px;border-radius:50%;background:var(--plum);color:var(--white);font-weight:500;font-size:29px;line-height:45px;display:flex;align-items:center;justify-content:center;text-align:center}
  .lead{position:absolute;left:409px;top:866px;width:640px;font-weight:300;font-size:45px;line-height:70px;color:var(--ink)}
  .card-icon{position:absolute;left:170px;top:1150px;width:192px;height:142px}
  .howto{position:absolute;left:400px;top:1102px;width:640px;font-weight:300;font-size:45px;line-height:70px;color:var(--ink)}
  .howto strong{color:var(--pink);font-weight:600}
  .continue{position:absolute;left:85px;top:1501px;width:1031px;height:241px;background:var(--pink);border-radius:0 0 58px 58px;color:var(--white);font-weight:600;font-size:48px;line-height:79px;text-align:center;padding-top:43px;text-transform:uppercase}
</style>
</head>
<body>
  <div class="backdrop" aria-hidden="true">
    <div class="band-top"></div>
    <div class="band-fade"></div>
    <div class="band-bottom"></div>
    <div class="blur bar-a"></div>
    <div class="blur bar-b"></div>
    <div class="blur bar-c"></div>
    <div class="blur side-l"></div>
    <div class="blur side-r"></div>
    <div class="blur pill"></div>
    <div class="blur glow"></div>
  </div>

  <div class="modal"></div>
  <h1 class="modal-title">Wed 25 Sept 8pm</h1>
  <svg class="close-btn" viewBox="0 0 120 120" aria-label="Close">
    <circle cx="60" cy="60" r="56" fill="none" stroke="#4f4350" stroke-width="6"/>
    <path d="M42 42 L78 78 M78 42 L42 78" stroke="#4f4350" stroke-width="7" stroke-linecap="round"/>
  </svg>

  <div class="brand-badge">Clover Draw<br>logo here</div>
  <p class="lead">Simply answer 5 questions correctly to win £20 credit!</p>

  <svg class="card-icon" viewBox="0 0 192 142" aria-hidden="true">
    <rect x="4" y="4" width="184" height="134" rx="14" fill="none" stroke="#f76d8f" stroke-width="6"/>
    <line x1="4" y1="50" x2="188" y2="50" stroke="#f76d8f" stroke-width="6"/>
    <line x1="24" y1="73" x2="84" y2="73" stroke="#f76d8f" stroke-width="5"/>
    <line x1="24" y1="87" x2="50" y2="87" stroke="#f76d8f" stroke-width="5"/>
    <line x1="140" y1="73" x2="166" y2="73" stroke="#f76d8f" stroke-width="5"/>
  </svg>
  <p class="howto">For the next 5 questions swipe right if your answer is <strong>YES</strong> or swipe left if your answer is <strong>NO</strong></p>

  <div class="continue">Swipe in any direction<br>to continue</div>
</body>
</html>
```